New Business Card Design Project

Need a design that will create an impact / strong impression towards our clients for our business. We are in the lighting business and we do lighting retrofits for large commercial to industrial clientele.

Target Market(s)

Lighting Industry

Industry/Entity Type

Business

Font styles to use
Other font styles liked:
• we would like to use the font on our logo, not sure what it is though..

Requirements
Must have
• Our logo.
Nice to have
• We are open to suggestions that have to do with lighting.

```html
<!DOCTYPE html>
<html lang="en">
<head>
<meta charset="utf-8">
<title>Brightline Retrofit Group – Business Card</title>
<link href="https://fonts.googleapis.com/css2?family=Open+Sans:wght@400;600;700&display=swap" rel="stylesheet">
<style>
  :root {
    --backdrop: #2b2b2b;
    --card-white: #ffffff;
    --card-green: #0a8234;
    --green-dark: #153f12;
    --green-mid: #0d8a3a;
    --green-light: #6cc24a;
    --green-title: #2e8b3e;
    --text-gray: #555555;
    --divider: #c8c8c8;
  }
  * { margin: 0; padding: 0; box-sizing: border-box; }
  html, body {
    width: 1200px; height: 960px; overflow: hidden;
    background: var(--backdrop);
    font-family: "Open Sans", Arial, sans-serif;
  }
  .canvas { position: relative; width: 1200px; height: 960px; }

  .card { position: absolute; width: 600px; height: 343px; overflow: hidden;
    box-shadow: 0 3px 6px rgba(0,0,0,0.45); }
  .card-front { left: 314px; top: 113px; background: var(--card-white); }
  .card-back { left: 311px; top: 472px; background: var(--card-green); }

  .brand { position: absolute; display: flex; align-items: center; gap: 10px;
    font-weight: 700; letter-spacing: 0.5px; }
  .brand-square { width: 16px; height: 16px; flex: none; }
  .card-front .brand { left: 44px; top: 138px; width: 250px; color: var(--green-dark);
    font-size: 20px; line-height: 25px; }
  .card-front .brand-name { display: block; }
  .card-front .brand-square { background: var(--green-mid); width: 20px; height: 20px; }
  .card-back .brand { left: 0; right: 0; justify-content: center; top: 152px;
    color: var(--card-white); font-size: 26px; white-space: nowrap; }
  .card-back .brand-square { background: var(--card-white); width: 22px; height: 22px; }

  .divider { position: absolute; left: 319px; top: 62px; width: 2px; height: 220px;
    background: linear-gradient(to bottom, rgba(200,200,200,0), var(--divider) 30%, var(--divider) 70%, rgba(200,200,200,0)); }

  .contact { position: absolute; left: 345px; top: 72px; color: var(--text-gray);
    font-size: 15.5px; line-height: 19px; }
  .contact-name { color: var(--green-dark); font-weight: 700; font-size: 20px; line-height: 24px; }
  .contact-title { color: var(--green-title); font-size: 17px; line-height: 20px; margin-bottom: 11px; }
  .contact-address { margin-bottom: 9px; }
  .contact-label { color: var(--green-dark); font-weight: 700; }
  .contact-web { letter-spacing: 1px; }

  .color-band { position: absolute; left: 0; top: 0; }

  .back-web { position: absolute; left: 0; right: 0; top: 281px; text-align: center;
    color: var(--card-white); font-size: 15px; letter-spacing: 2px; }
</style>
</head>
<body>
<div class="canvas">

  <section class="card card-front">
    <div class="brand"><span class="brand-square"></span><span class="brand-name">Brightline Retrofit Group, LLC</span></div>
    <div class="divider"></div>
    <div class="contact">
      <div class="contact-name">DANIEL REYES</div>
      <div class="contact-title">CEO/FOUNDER</div>
      <div class="contact-address">1420 Cedar Ridge Road<br>Fairbanks, Alaska 99701</div>
      <div><span class="contact-label">P :</span> 907 555 0142</div>
      <div><span class="contact-label">M :</span> 907 555 0187</div>
      <div><span class="contact-label">F :</span> 907 555 0163</div>
      <div>info@brightlineretrofit.com</div>
      <div class="contact-web">www.brightlineretrofit.com</div>
    </div>
    <svg class="color-band" width="600" height="343" viewBox="0 0 600 343" aria-hidden="true">
      <polygon points="0,343 0,343 99,337.4 99,343" fill="var(--green-light)"/>
      <polygon points="101,343 101,337.3 199,331.7 199,343" fill="var(--green-mid)"/>
      <polygon points="201,343 201,331.6 299,326.1 299,343" fill="var(--green-dark)"/>
      <polygon points="301,343 301,325.9 400,320.3 400,343" fill="var(--green-light)"/>
      <polygon points="402,343 402,320.2 500,314.6 500,343" fill="var(--green-mid)"/>
      <polygon points="502,343 502,314.5 600,309 600,343" fill="var(--green-dark)"/>
    </svg>
  </section>

  <section class="card card-back">
    <div class="brand"><span class="brand-square"></span>Brightline Retrofit Group, LLC</div>
    <div class="back-web">www.brightlineretrofitgroup.com</div>
  </section>

</div>
</body>
</html>
```